FinTech company looking to revamp and expand client-facing interface for our financial models

Pellworth Engines currently has a very simple website that allows clients to interact with our financial models. We are looking to completely redesign the current site and add several extra pages to provide extra functionality. We want the design to have a modern, slick feel, that will work on both a desktop or a tablet. It should be straightforward for clients to move between different pages at any time, and clear from the layout how to interact with the more advanced features. We have included screenshots of existing pages in the attached design brief, as well as sketches of the functionality required by the new pages, but can't provide a direct link to the current site.
Target Market(s)
Professional investors that will be paying to access the interface
Industry/Entity Type
Finance
Number of Pages Required
4 page
Colors
Designer to choose colors to be used in the design.
Look and feel
Each slider illustrates characteristics of the customer's brand and the style your logo design should communicate.

```html
<!DOCTYPE html>
<html lang="en">
<head>
<meta charset="utf-8">
<title>Pellworth Engines – Portfolio</title>
<link href="https://fonts.googleapis.com/css2?family=Open+Sans:wght@400;600;700&display=swap" rel="stylesheet">
<style>
:root{
  --teal:#0b7a73;
  --teal-dark:#0a5e59;
  --navy:#0d3a73;
  --green:#2c8a2c;
  --red:#c0262e;
  --ink:#1d1d1d;
  --muted:#666;
  --line:#e3e3e3;
  --row-alt:#f0f0f0;
  --row-hover:#6f6f6f;
  --page:#f4f4f4;
  --card-dark:#2d2d2d;
}
*{box-sizing:border-box;margin:0;padding:0}
html,body{width:1200px;height:1149px;overflow:hidden;background:#fff;font-family:'Open Sans',sans-serif;color:var(--ink)}
.stage{position:relative;width:1300px;height:1245px;transform:scale(0.9231);transform-origin:0 0}
.abs{position:absolute}
.topbar{left:0;top:0;width:1300px;height:60px;background:#fff;display:flex;align-items:stretch}
.brand{width:195px;display:flex;align-items:center;padding-left:72px;font-weight:700;font-size:19px}
.tab{display:flex;align-items:center;justify-content:center;font-weight:700;font-size:14px;border-left:1px solid var(--line)}
.tab.range{width:90px}
.spacer{flex:1;border-left:1px solid var(--line)}
.nav{padding:0 24px;gap:10px}
.nav.active{background:var(--teal);color:#fff}
.page{left:0;top:60px;width:1300px;height:1185px;background:var(--page)}
.card{background:#fff;border-radius:4px;overflow:hidden}
.members{left:70px;top:100px;width:560px;height:520px}
.card-head{height:50px;background:var(--card-dark);color:#fff;font-weight:600;font-size:17px;display:flex;align-items:center;justify-content:center}
.sub-head{height:50px;background:var(--teal);color:#fff;font-weight:600;font-size:16px;display:flex;align-items:center;padding-left:60px}
.member-row{height:70px;display:flex;align-items:center;padding-left:50px;gap:14px;font-size:17px;color:var(--muted)}
.btn{display:flex;align-items:center;gap:8px;color:#fff;font-weight:700;font-size:15px;border-radius:4px;padding:0 16px}
.btn-add{background:var(--navy)}
.btn-save{background:var(--green)}
.sens{left:670px;top:100px;width:560px;height:340px}
.sens .card-head{height:70px;background:var(--teal-dark)}
.bar-row{position:absolute;left:260px;width:275px;height:40px;border:1px solid var(--line);background:#fafafa}
.chart{left:70px;top:740px;width:1160px;height:425px}
.chart-tab{left:55px;top:50px;width:155px;height:35px;background:var(--teal);color:#fff;font-weight:600;font-size:16px;display:flex;align-items:center;justify-content:center}
.overlay{left:0;top:60px;width:1300px;height:1185px;background:rgba(20,20,20,0.8)}
.modal{left:370px;top:150px;width:560px;height:670px;background:#fff;border-radius:4px;overflow:hidden}
.modal-head{height:50px;background:var(--teal);color:#fff;font-weight:600;font-size:17px;display:flex;align-items:center;justify-content:center}
.field-row{position:absolute;left:0;width:560px;height:50px;display:flex;align-items:center}
.field-label{width:191px;padding-left:28px;font-weight:700;font-size:17px}
.input{width:229px;height:31px;border:1px solid #bbb;border-radius:3px;display:flex;align-items:center;padding:0 12px;font-size:15px;justify-content:space-between;box-shadow:inset 0 1px 2px rgba(0,0,0,.15)}
.btn-search{margin-left:9px;width:106px;height:31px;background:var(--navy);color:#fff;font-weight:700;font-size:15px;border-radius:3px;display:flex;align-items:center;justify-content:center}
.results-head{left:0;top:200px;width:560px;height:50px;display:flex;align-items:center;justify-content:space-between;padding:0 42px 0 27px;font-size:17px;font-weight:600}
.select-all{display:flex;align-items:center;gap:8px;font-weight:700;font-size:16px}
.check{width:19px;height:19px;border:1px solid #aaa;border-radius:3px;background:#fff}
.list{left:0;top:250px;width:520px;height:350px}
.result{height:70px;display:flex;align-items:center;padding-left:27px;font-size:17px;background:#fff}
.result.alt{background:var(--row-alt)}
.result.hover{background:var(--row-hover);color:#fff}
.scroll{left:520px;top:250px;width:40px;height:350px;background:#c8c8c8}
.scroll-track{position:absolute;left:11px;top:25px;width:18px;height:298px;background:#fff;border-radius:9px}
.scroll-thumb{position:absolute;left:11px;top:25px;width:18px;height:74px;background:#8a8a8a;border-radius:9px}
.modal-foot{left:0;top:600px;width:560px;height:70px;background:#efefef;display:flex;align-items:center;justify-content:center}
.modal-foot .btn{height:40px;font-size:16px}
</style>
</head>
<body>
<div class="stage">
  <header class="abs topbar">
    <div class="brand">KORVAL</div>
    <div class="tab range">250D</div>
    <div class="tab range">83D</div>
    <div class="tab range">42D</div>
    <div class="spacer"></div>
    <div class="tab nav" style="width:140px">
      <svg width="24" height="22" viewBox="0 0 24 22"><path d="M2 11 12 2l10 9M5 9v11h5v-6h4v6h5V9" fill="none" stroke="#1d1d1d" stroke-width="2.4"/></svg>MODELS</div>
    <div class="tab nav" style="width:177px">
      <svg width="26" height="26" viewBox="0 0 26 26" fill="#1d1d1d"><circle cx="13" cy="13" r="3"/><circle cx="13" cy="4" r="2"/><circle cx="13" cy="22" r="2"/><circle cx="4" cy="13" r="2"/><circle cx="22" cy="13" r="2"/><circle cx="6.5" cy="6.5" r="2"/><circle cx="19.5" cy="19.5" r="2"/><circle cx="19.5" cy="6.5" r="2"/><circle cx="6.5" cy="19.5" r="2"/></svg>SENSITIVITIES</div>
    <div class="tab nav active" style="width:161px">
      <svg width="24" height="24" viewBox="0 0 24 24" fill="none" stroke="#fff" stroke-width="2"><circle cx="6" cy="6" r="4"/><circle cx="18" cy="6" r="4"/><circle cx="6" cy="18" r="4"/><circle cx="18" cy="18" r="4"/></svg>PORTFOLIO</div>
    <div class="tab nav" style="width:151px;border-right:1px solid var(--line)">
      <svg width="26" height="22" viewBox="0 0 26 22" fill="none" stroke="#1d1d1d" stroke-width="2"><rect x="1" y="1" width="24" height="20"/><path d="M4 16l5-6 4 4 5-8 4 5"/></svg>BACKTEST</div>
  </header>

  <main class="abs page"></main>

  <section class="abs card members">
    <div class="card-head">Current Members</div>
    <div class="sub-head">Members Name</div>
    <div class="member-row"><svg width="24" height="24"><circle cx="12" cy="12" r="10" fill="none" stroke="var(--red)" stroke-width="2"/><path d="M7 12h10" stroke="var(--red)" stroke-width="2"/></svg>Member 1</div>
    <div class="member-row"><svg width="24" height="24"><circle cx="12" cy="12" r="10" fill="none" stroke="var(--red)" stroke-width="2"/><path d="M7 12h10" stroke="var(--red)" stroke-width="2"/></svg>Member 2</div>
    <div class="member-row"><svg width="24" height="24"><circle cx="12" cy="12" r="10" fill="none" stroke="var(--red)" stroke-width="2"/><path d="M7 12h10" stroke="var(--red)" stroke-width="2"/></svg>Member 3</div>
    <div class="member-row"><svg width="24" height="24"><circle cx="12" cy="12" r="10" fill="none" stroke="var(--red)" stroke-width="2"/><path d="M7 12h10" stroke="var(--red)" stroke-width="2"/></svg>Member 4</div>
    <div class="member-row"><svg width="24" height="24"><circle cx="12" cy="12" r="10" fill="none" stroke="var(--red)" stroke-width="2"/><path d="M7 12h10" stroke="var(--red)" stroke-width="2"/></svg>Member 5</div>
    <div class="member-row"><svg width="24" height="24"><circle cx="12" cy="12" r="10" fill="none" stroke="var(--red)" stroke-width="2"/><path d="M7 12h10" stroke="var(--red)" stroke-width="2"/></svg>Member 6</div>
  </section>
  <div class="abs btn btn-add" style="left:70px;top:640px;height:40px;width:178px">
    <svg width="20" height="20"><circle cx="10" cy="10" r="9" fill="none" stroke="#fff" stroke-width="1.6"/><path d="M10 5v10M5 10h10" stroke="#fff" stroke-width="1.6"/></svg>ADD MEMBERS</div>
  <div class="abs btn btn-save" style="left:257px;top:640px;height:40px;width:200px">
    <svg width="22" height="18"><path d="M2 9l6 6L20 2" fill="none" stroke="#fff" stroke-width="3"/></svg>SAVE PORTFOLIO</div>

  <section class="abs card sens">
    <div class="card-head">Sensitivities</div>
    <div class="bar-row" style="top:85px"><div class="abs" style="left:114px;top:0;width:68px;height:38px;background:var(--green)"></div><span class="abs" style="left:195px;top:8px;font-size:17px;color:#555">0.9</span></div>
    <div class="bar-row" style="top:155px"><div class="abs" style="left:114px;top:0;width:54px;height:38px;background:var(--green)"></div><span class="abs" style="left:181px;top:8px;font-size:17px;color:#555">0.7</span></div>
    <div class="bar-row" style="top:225px"><div class="abs" style="left:74px;top:0;width:40px;height:38px;background:var(--red)"></div><span class="abs" style="left:36px;top:8px;font-size:17px;color:#555">-0.6</span></div>
    <div class="bar-row" style="top:295px"><div class="abs" style="left:96px;top:0;width:18px;height:38px;background:var(--red)"></div><span class="abs" style="left:57px;top:8px;font-size:17px;color:#555">-0.3</span></div>
    <div class="abs" style="left:374px;top:80px;width:2px;height:255px;background:#999"></div>
  </section>

  <section class="abs card chart">
    <div class="abs chart-tab">Chart</div>
    <div class="abs" style="left:250px;top:58px;font-size:16px;color:#555">#1</div>
    <div class="abs" style="left:55px;top:84px;width:1070px;height:2px;background:var(--line)"></div>
    <svg class="abs" style="left:50px;top:130px" width="1100" height="240" viewBox="0 0 1100 240" role="img" aria-label="Scatter chart of member scores over time">
      <g font-size="11" fill="#777" font-family="Open Sans, sans-serif">
        <text x="10" y="22">100</text><text x="16" y="59">80</text><text x="16" y="96">60</text><text x="16" y="134">40</text><text x="16" y="171">20</text><text x="22" y="209">0</text>
        <text x="40" y="230">Jul 2018</text><text x="180" y="230">Sep 2018</text><text x="320" y="230">Nov 2018</text><text x="462" y="230">Jan 2019</text><text x="596" y="230">Mar 2019</text><text x="736" y="230">May 2019</text><text x="880" y="230">Jul 2019</text>
        <text x="1012" y="20">Names</text>
      </g>
      <line x1="35" y1="205" x2="955" y2="205" stroke="#bbb"/>
      <line x1="80" y1="18" x2="290" y2="18" stroke="#b8c23a" stroke-width="6" stroke-dasharray="3 2"/>
      <line x1="470" y1="18" x2="908" y2="18" stroke="#2b5aa0" stroke-width="6" stroke-dasharray="3 2"/>
      <g fill="#2b5aa0">
        <circle cx="85" cy="30" r="3"/><circle cx="100" cy="28" r="3"/><circle cx="82" cy="84" r="3"/><circle cx="104" cy="100" r="3"/><circle cx="110" cy="130" r="3"/><circle cx="120" cy="150" r="3"/><circle cx="135" cy="96" r="3"/><circle cx="148" cy="98" r="3"/><circle cx="145" cy="122" r="3"/><circle cx="165" cy="130" r="3"/><circle cx="180" cy="150" r="3"/><circle cx="195" cy="155" r="3"/><circle cx="215" cy="185" r="3"/><circle cx="230" cy="180" r="3"/><circle cx="250" cy="184" r="3"/><circle cx="265" cy="160" r="3"/><circle cx="285" cy="150" r="3"/><circle cx="300" cy="165" r="3"/><circle cx="315" cy="200" r="3"/><circle cx="345" cy="50" r="3"/><circle cx="352" cy="70" r="3"/><circle cx="360" cy="40" r="3"/><circle cx="370" cy="55" r="3"/><circle cx="380" cy="185" r="3"/><circle cx="395" cy="160" r="3"/><circle cx="405" cy="140" r="3"/><circle cx="415" cy="125" r="3"/><circle cx="422" cy="38" r="3"/><circle cx="435" cy="25" r="3"/><circle cx="450" cy="32" r="3"/><circle cx="888" cy="202" r="3"/>
      </g>
      <g fill="#b8c23a">
        <circle cx="170" cy="30" r="3"/><circle cx="185" cy="25" r="3"/><circle cx="210" cy="28" r="3"/><circle cx="218" cy="85" r="3"/><circle cx="230" cy="97" r="3"/><circle cx="225" cy="130" r="3"/><circle cx="240" cy="118" r="3"/><circle cx="255" cy="112" r="3"/><circle cx="262" cy="80" r="3"/><circle cx="275" cy="45" r="3"/><circle cx="282" cy="20" r="3"/><circle cx="295" cy="100" r="3"/><circle cx="310" cy="150" r="3"/><circle cx="322" cy="178" r="3"/><circle cx="338" cy="150" r="3"/><circle cx="350" cy="188" r="3"/><circle cx="365" cy="195" r="3"/><circle cx="390" cy="150" r="3"/><circle cx="408" cy="100" r="3"/><circle cx="420" cy="20" r="3"/><circle cx="455" cy="192" r="3"/><circle cx="475" cy="192" r="3"/><circle cx="490" cy="180" r="3"/><circle cx="505" cy="186" r="3"/><circle cx="520" cy="180" r="3"/><circle cx="535" cy="155" r="3"/><circle cx="540" cy="125" r="3"/><circle cx="545" cy="82" r="3"/><circle cx="552" cy="40" r="3"/><circle cx="570" cy="40" r="3"/><circle cx="580" cy="160" r="3"/><circle cx="595" cy="70" r="3"/><circle cx="602" cy="120" r="3"/><circle cx="615" cy="38" r="3"/><circle cx="630" cy="30" r="3"/>
      </g>
      <g>
        <circle cx="997" cy="17" r="3" fill="#b8c23a"/><circle cx="997" cy="36" r="3" fill="#b8c23a"/><circle cx="997" cy="55" r="3" fill="#2c8a2c"/><circle cx="997" cy="73" r="3" fill="#9b5aa0"/><circle cx="997" cy="92" r="3" fill="#9b5aa0"/><circle cx="997" cy="110" r="3" fill="#aaa"/><circle cx="997" cy="129" r="3" fill="#b8c23a"/><circle cx="997" cy="147" r="3" fill="#b8c23a"/><circle cx="997" cy="166" r="3" fill="#2c8a2c"/><circle cx="997" cy="185" r="3" fill="#3aa0a0"/><circle cx="997" cy="203" r="3" fill="#2b5aa0"/>
      </g>
    </svg>
  </section>

  <div class="abs overlay"></div>

  <section class="abs modal" aria-label="Add Members">
    <div class="modal-head">Add Members</div>
    <div class="field-row" style="top:50px;border-bottom:1px solid var(--line)">
      <div class="field-label">Search Database</div>
      <div class="input">Name</div>
      <div class="btn-search">Search</div>
    </div>
    <div class="field-row" style="top:100px">
      <div class="field-label">Filter by Sector</div>
      <div class="input">Select sector<svg width="16" height="9"><path d="M0 0h16L8 9z" fill="#333"/></svg></div>
      <div class="btn-search">Search</div>
    </div>
    <div class="abs results-head">Search Results<div class="select-all"><div class="check"></div>Select All</div></div>
    <div class="abs" style="left:0;top:250px;width:560px;height:1px;background:var(--line)"></div>
    <div class="abs list">
      <div class="result">Member 1</div>
      <div class="result hover">Member 2</div>
      <div class="result">Member 3</div>
      <div class="result alt">Member 4</div>
      <div class="result">Member 5</div>
    </div>
    <div class="abs scroll"><div class="scroll-track"></div><div class="scroll-thumb"></div></div>
    <div class="abs modal-foot">
      <div class="btn btn-add">
        <svg width="22" height="22"><circle cx="11" cy="11" r="9.5" fill="none" stroke="#fff" stroke-width="1.6"/><path d="M11 6v10M6 11h10" stroke="#fff" stroke-width="1.6"/></svg>ADD MEMBERS</div>
    </div>
  </section>
</div>
</body>
</html>
```